Executive Business Card for Healthcare Company [Need Today]

I need a business card design for a healthcare company. The only branding the company has thus far is a logo. The cards will be utilized by company executives. The design I envision will be vibrant and appealing but with a corporate feel. They shouldn't be too casual or playful. I would like to complete this project TODAY if possible.

Target Market(s)

Healthcare vendors, other executives in healthcare and pharmaceuticals

Industry/Entity Type

Pharmaceutical

Contact Information for Business Card

See attachment

Font styles to use
Serif
Sans Serif

Colors

Designer to choose colors to be used in the design.

```html
<!DOCTYPE html>
<html lang="en">
<head>
<meta charset="utf-8">
<title>Corvane Therapeutics – Business Card</title>
<link href="https://fonts.googleapis.com/css2?family=Raleway:wght@300;400;500&display=swap" rel="stylesheet">
<style>
  :root {
    --bg: #e8e9ea;
    --card: #ffffff;
    --teal: #1fa3b3;
    --green: #4daf8a;
    --ink: #4a4d50;
    --ink-soft: #7a7d80;
    --rule: #b9bcbe;
  }
  * { margin: 0; padding: 0; box-sizing: border-box; }
  html, body { width: 1200px; height: 726px; overflow: hidden; }
  body {
    background: var(--bg);
    font-family: "Raleway", Arial, sans-serif;
    position: relative;
  }
  .card {
    position: absolute;
    top: 214px;
    width: 520px;
    height: 297px;
    background: var(--card);
    overflow: hidden;
    box-shadow: 0 2px 6px rgba(0,0,0,0.08);
  }
  .card--front { left: 50px; }
  .card--back { left: 630px; }

  /* Front */
  .front-brand {
    position: absolute;
    top: 92px;
    left: 0;
    width: 100%;
    display: flex;
    align-items: center;
    justify-content: center;
    gap: 18px;
  }
  .brand-dot {
    width: 54px; height: 54px;
    border-radius: 50%;
    border: 3px solid var(--green);
  }
  .brand-divider {
    width: 1px; height: 56px;
    background: var(--rule);
  }
  .wordmark {
    color: var(--teal);
    font-weight: 400;
    line-height: 1.05;
  }
  .wordmark__name { display: block; }
  .front-brand .wordmark { font-size: 30px; }
  .front-brand .wordmark__sub { font-size: 20px; display: block; }
  .website {
    position: absolute;
    bottom: 58px;
    width: 100%;
    text-align: center;
    font-size: 13px;
    letter-spacing: 3px;
    color: var(--ink);
    font-weight: 400;
  }
  .website__domain { color: var(--teal); }

  /* Back */
  .back-ring {
    position: absolute;
    left: -70px;
    top: 40px;
    width: 320px;
    height: 320px;
  }
  .back-brand {
    position: absolute;
    top: 26px;
    right: 30px;
    text-align: right;
  }
  .back-brand .wordmark { font-size: 26px; }
  .back-brand .wordmark__sub { font-size: 18px; display: block; }
  .contact {
    position: absolute;
    left: 280px;
    top: 116px;
    color: var(--ink);
  }
  .contact__name {
    font-size: 20px;
    font-weight: 500;
    color: var(--teal);
  }
  .contact__title {
    font-size: 10px;
    color: var(--ink-soft);
    margin: 3px 0 12px;
  }
  .contact__list { list-style: none; font-size: 12.5px; line-height: 20px; }
  .contact__list li { display: flex; align-items: center; gap: 8px; }
  .contact__list svg { width: 12px; height: 12px; flex: none; }
  .contact__list .no-icon { padding-left: 20px; }
</style>
</head>
<body>
  <section class="card card--front" aria-label="Card front">
    <div class="front-brand">
      <span class="brand-dot"></span>
      <span class="brand-divider"></span>
      <div class="wordmark">
        <span class="wordmark__name">Corvane</span>
        <span class="wordmark__sub">Therapeutics</span>
      </div>
    </div>
    <p class="website">www.<span class="website__domain">corvanerx</span>.com</p>
  </section>

  <section class="card card--back" aria-label="Card back">
    <svg class="back-ring" viewBox="0 0 320 320" aria-hidden="true">
      <circle cx="160" cy="160" r="152" fill="none" stroke="var(--green)" stroke-width="6"/>
    </svg>
    <div class="back-brand">
      <div class="wordmark">
        <span class="wordmark__name">Corvane</span>
        <span class="wordmark__sub">Therapeutics</span>
      </div>
    </div>
    <div class="contact">
      <p class="contact__name">Daniel Hale</p>
      <p class="contact__title">Senior Director of Marketing</p>
      <ul class="contact__list">
        <li>
          <svg viewBox="0 0 12 12" aria-hidden="true"><path d="M2 1h2.5l1 3-1.5 1a7 7 0 0 0 3 3l1-1.5 3 1V10a1 1 0 0 1-1 1A9 9 0 0 1 1 2a1 1 0 0 1 1-1z" fill="var(--ink)"/></svg>
          555-014-2280
        </li>
        <li>
          <svg viewBox="0 0 12 12" aria-hidden="true"><rect x="3" y="0.5" width="6" height="11" rx="1" fill="none" stroke="var(--ink)"/><circle cx="6" cy="9.5" r="0.7" fill="var(--ink)"/></svg>
          555-014-7716
        </li>
        <li>
          <svg viewBox="0 0 12 12" aria-hidden="true"><circle cx="6" cy="6" r="5" fill="none" stroke="var(--ink)"/><path d="M1 6h10M6 1c-2.5 3-2.5 7 0 10M6 1c2.5 3 2.5 7 0 10" fill="none" stroke="var(--ink)" stroke-width="0.8"/></svg>
          dhale@corvanerx.com
        </li>
        <li class="no-icon">118 Linden Avenue</li>
        <li class="no-icon">Fairview, GA 30000</li>
      </ul>
    </div>
  </section>
</body>
</html>
```